Private Investigation Business Card Design

I need a business card for a new private investigation company named Brisk Inquiries. I perform mainly surveillance jobs, vehicle repossessions, document serves etc. The final design should aim for a professional look. The logo has a magnifying glass with stick man arms and legs and is in a running action to show the "Brisk" aspect of the name. If the colour scheme could remain the same as the website www.briskinquiries-demo.com.au with silvers,blacks and a couple electric blue highlights.
Industry/Entity Type
Business
Contact Information for Business Card
Morgan Kellaway
Brisk Inquiries
0487316204
PO Box 58, Carnwell NSW 2291
info@briskinquiries-demo.com.au
www.briskinquiries-demo.com.au
Look and feel

```html
<!DOCTYPE html>
<html lang="en">
<head>
<meta charset="utf-8">
<title>Brisk Inquiries – Business Card</title>
<link rel="stylesheet" href="https://fonts.googleapis.com/css2?family=Exo+2:wght@400;600&display=swap">
<style>
  :root {
    --stage: #3a3a3a;
    --card-dark: #000000;
    --card-light: #ffffff;
    --silver: #d6d6d6;
    --silver-strong: #e4e4e4;
    --grey-text: #555555;
    --brand-silver: #9a9a9a;
    --art-light: #ffffff;
    --art-mid: #e2e2e2;
  }
  * { box-sizing: border-box; margin: 0; padding: 0; }
  html, body { width: 1200px; height: 750px; overflow: hidden; }
  body {
    background: var(--stage);
    font-family: "Exo 2", Arial, sans-serif;
    position: relative;
  }
  .card {
    position: absolute;
    top: 228px;
    width: 461px;
    height: 262px;
    overflow: hidden;
  }
  .card--front { left: 124px; background: var(--card-dark); }
  .card--back { left: 618px; background: var(--card-light); }

  .front__art {
    position: absolute;
    left: 0; top: 0;
    width: 254px; height: 262px;
    background: linear-gradient(160deg, var(--art-light) 0%, var(--art-light) 55%, var(--art-mid) 100%);
    clip-path: polygon(0 0, 124px 0, 150px 130px, 254px 262px, 0 262px);
  }
  .front__details {
    position: absolute;
    right: 24px; top: 27px;
    text-align: right;
    color: var(--silver);
  }
  .front__name {
    font-size: 16px;
    font-weight: 600;
    letter-spacing: 0.4px;
    color: var(--silver-strong);
    margin-bottom: 12px;
  }
  .front__address { font-size: 11px; line-height: 16px; margin-bottom: 6px; }
  .contact-line {
    display: flex;
    justify-content: flex-end;
    align-items: center;
    gap: 7px;
    font-size: 10.5px;
    line-height: 17.5px;
  }
  .contact-line--phone { font-size: 12px; }
  .contact-line svg { width: 11px; height: 11px; fill: var(--silver); flex: none; }
  .front__brand {
    position: absolute;
    right: 24px; top: 188px;
    font-size: 28px;
    font-weight: 600;
    color: var(--brand-silver);
    letter-spacing: 0.5px;
  }

  .back__brand {
    position: absolute;
    left: 0; right: 0; top: 106px;
    display: flex;
    justify-content: center;
    align-items: center;
    gap: 12px;
    font-size: 34px;
    font-weight: 600;
    color: var(--brand-silver);
  }
  .back__mark {
    width: 20px; height: 20px;
    border-radius: 50%;
    background: var(--brand-silver);
  }
  .back__web {
    position: absolute;
    left: 0; right: 0; top: 218px;
    text-align: center;
    font-size: 10px;
    letter-spacing: 2px;
    color: var(--grey-text);
  }
</style>
</head>
<body>
  <section class="card card--front">
    <div class="front__art" role="img" aria-label="Running magnifying-glass mascot with speed lines"></div>
    <div class="front__details">
      <p class="front__name">Morgan Kellaway</p>
      <p class="front__address">PO Box 58<br>Carnwell NSW 2291</p>
      <p class="contact-line contact-line--phone">0487 316 204
        <svg viewBox="0 0 24 24" aria-hidden="true"><path d="M6.6 10.8a15 15 0 0 0 6.6 6.6l2.2-2.2c.3-.3.7-.4 1-.2 1.1.4 2.3.6 3.6.6.6 0 1 .4 1 1V20c0 .6-.4 1-1 1A17 17 0 0 1 3 4c0-.6.4-1 1-1h3.5c.6 0 1 .4 1 1 0 1.3.2 2.5.6 3.6.1.3 0 .7-.2 1z"/></svg>
      </p>
      <p class="contact-line">info@briskinquiries-demo.com.au
        <svg viewBox="0 0 24 24" aria-hidden="true"><path d="M2 5h20v14H2zm2 2v.5l8 5 8-5V7zm0 3v7h16v-7l-8 5z"/></svg>
      </p>
      <p class="contact-line">www.briskinquiries-demo.com.au
        <svg viewBox="0 0 24 24" aria-hidden="true"><path d="M12 2a10 10 0 1 0 0 20 10 10 0 0 0 0-20zm0 2c1 0 2.3 2 2.8 5H9.2C9.7 6 11 4 12 4zM4.3 11h4.7a17 17 0 0 0 0 2H4.3a8 8 0 0 1 0-2zm6.7 0h2a15 15 0 0 1 0 2h-2a15 15 0 0 1 0-2zm4 0h4.7a8 8 0 0 1 0 2H15a17 17 0 0 0 0-2zm-5.8 4h5.6c-.5 3-1.8 5-2.8 5s-2.3-2-2.8-5z"/></svg>
      </p>
    </div>
    <p class="front__brand">Brisk Inquiries</p>
  </section>

  <section class="card card--back">
    <div class="back__brand">Brisk Inquiries <span class="back__mark"></span></div>
    <p class="back__web">www.briskinquiries-demo.com.au</p>
  </section>
</body>
</html>
```